Verpackungen für Shampoos
Zielgruppe
Wir sind ein kleines Familienunternehmen mit 2-3 Friseurfilialen und Onlineshop im Naturfriseurbereich, arbeiten mit ökologischen, nachhaltigen und natürlichen Produkten und vertreiben unsere eigene Haarbürste. Wir betreiben mit Sol Verde unsere eigene Marke in diesem Bereich. Erste Produkte, wie eine eigene Haarbürste sind bereits vorhanden und entstanden.
Für unsere erste Shampoo Serie suchen wir ein klares, cleanes und hochwertiges Design. Die 200ml Shampooflasche kommt komplett in weiß und besteh aus recyceltem Material. Es soll klar die ökologisch nachhaltige und etwas höherpreisige Marke kommuniziert werden. Dabei sehen wir vom Stil „weniger ist mehr“ als ganz klare Designvorgabe. Anbei auch ein Beispiel von Pavura, die das ganze sehr schön umgesetzt haben.
Die INCI sind noch nicht final. Es wäre schön, wenn hier ein Platzhalter eingefügt würde. Da eine der Hauptzielgruppen auch Österreicher sind, würden wir uns über ein kleines „Made in Austria“ auf der Vorderseite (evtl. ganz unten auf der Flasche) freuen.
Insgesamt sind es vier verschiedene Shampoos, die aus der gleichen Serie stammen. Es wäre schön, wenn man diese auch direkt unterscheiden könnte. Vielleicht durch ein grafisches Element, oder einfach nur durch die verschiedenen Namenserweiterungen. Hier die Aufstellung mit den Erweiterungen:
Es werden 4 verschiedene Shampoos, die Namen sind:
Change - Strapaziertes Haar
Care - Normales Haar
Sensitiv - Empfindliche Kopfhaut
Balancing - Fettiges Haar
Zielgruppe:
Weiblich, 30-60 Jahre, mittleres bis gehobenes Einkommen, nachhaltig, ökologisch, natürlich, legt Wert auf hochwertige Produkte und Dienstleistungen, achtet auf Konsum.
Aufgabenstellung
Die Landingpage zur Bürste ist hier erreichbar (Beispiel):
Vielleicht hilft das etwas um das Design und die Tonality aufzuschnappen: https://sol-verde.de/gold-birch-wildschweinborstenbuerste/
Es wäre super, wenn das Design der Flasche ähnlich klar und strukturiert ist.
Die Shampoos sind komplett vegan und made in Austria. Die beiden Aspekte sollten in Design auch aufgegriffen werden. Da wir einen 4 farbigen Tamponade/Siebdruck auf der Flasche anwenden, stehen leider nicht so viele Farben zur Verfügung (3-4).
Link zur Flasche:
https://www.brumoxa.com/de/kosmetik/varleno/varleno-tubica/flasche-heavy-200ml-24-410-plastik
Des Weiteren kann sich noch am Sol Verde Haarkonzept und unserem Dienstleistungsflyer orientiert werden.
Benefits:
-       Pflegt das Haar, hält es geschmeidig
- Bio Shampoo Konzentrat
-       Die Grundlage für gesunde Kopfhaut und schönes Haar*
-       Vermindert Spliss*
-       Hält die Haare natürlich geschmeidig
-       Regt die Durchblutung der Kopfhaut an
-       Verteilt Nährstoffe von der Wurzel bis in die Spitzen*
-       Verbessert das Kopfhautklima*
-       Für eine gut durchblutete und gesunde Kopfhaut mit glänzenden und
geschmeidigen Haaren*
-       Entfernt Schuppen und abgestorbene Hautpartikel
-       Verbessert natürlich die allgemeine Haarstruktur
-       Entwirrt langes und gelocktes Haar
-       Reinigt die Kopfhaut ohne Chemie*
-       Mehr Volumen im Haar
-       Mehr Stand im Haar durch Kräftigung der Haarbalkmuskulatur
-       Spart Shampoo und hilft Shampoo seltener und weniger zu nutzen
-       Nährstoffversorgung bis in die Haarspitzen
Inhaltsstoffe:
Care
Aloe Vera Direktsaft*, Decyl Glucoside, Coco Glucoside, Lauryl Glucoside, Hopfenextrakt*, Pentylene Glycol green, Meli..

```html
<!DOCTYPE html>
<html lang="de">
<head>
<meta charset="utf-8">
<title>Sol Verde – Shampoo Etiketten</title>
<link rel="stylesheet" href="https://fonts.googleapis.com/css2?family=Quicksand:wght@400;500&display=swap">
<style>
  :root {
    --stage: #f3f3f3;
    --label: #ffffff;
    --ink: #111111;
    --brand: #2e3192;
    --peach: #fbd7a1;
    --sage: #b9d9ab;
    --sage-soft: #c6dfb4;
  }
  * { margin: 0; padding: 0; box-sizing: border-box; }
  html, body {
    width: 1200px; height: 1200px; overflow: hidden;
    background: var(--stage);
    font-family: "Quicksand", sans-serif;
    color: var(--ink);
  }
  .stage { position: relative; width: 1200px; height: 1200px; }
  .label {
    position: absolute;
    width: 463px; height: 1051px;
    background: var(--label);
    overflow: hidden;
    box-shadow: 4px 6px 14px rgba(0,0,0,0.18);
  }
  .label--care { left: 97px; top: 65px; }
  .label--balance { left: 623px; top: 68px; }
  .label__shapes { position: absolute; inset: 0; width: 463px; height: 1051px; }
  .brand {
    position: absolute; left: 148px; top: 116px;
    font-family: "Quicksand", sans-serif;
    font-weight: 500; font-size: 25px; line-height: 1;
    color: var(--brand);
    letter-spacing: 0.5px;
  }
  .product {
    position: absolute; left: 0; width: 100%;
    text-align: center;
  }
  .product__name {
    display: block;
    font-weight: 500; line-height: 1;
    letter-spacing: 1px;
  }
  .product__type {
    display: block;
    font-weight: 400; font-size: 27px; letter-spacing: 0.5px;
  }
  .product__kind {
    display: block; margin-top: 6px;
    font-weight: 400; font-size: 16px; font-style: italic;
  }
  .label--care .product { top: 338px; }
  .label--care .product__name { font-size: 82px; }
  .label--care .product__type { margin-top: 14px; }
  .label--balance .product { top: 366px; }
  .label--balance .product__name { font-size: 65px; }
  .label--balance .product__type { margin-top: 12px; }
  .artwork { position: absolute; }
  .volume {
    position: absolute; left: 0; width: 100%; top: 982px;
    text-align: center; font-size: 15px; font-weight: 500;
  }
</style>
</head>
<body>
<main class="stage">

  <section class="label label--care">
    <svg class="label__shapes" viewBox="0 0 463 1051" aria-hidden="true">
      <path fill="var(--peach)" d="M48 0 L305 0 C307 52 280 80 225 80 C182 80 166 60 152 45 C140 32 130 30 115 35 C95 42 80 48 62 43 C48 38 48 20 48 0Z"/>
      <path fill="var(--sage)" d="M320 285 C345 282 370 305 371 335 C372 352 360 362 340 360 C318 358 312 346 324 336 C333 328 320 320 305 312 C290 302 300 288 320 285Z"/>
    </svg>
    <div class="brand">Sol Verde</div>
    <div class="product">
      <span class="product__name">Care</span>
      <span class="product__type">Normales Haar</span>
      <span class="product__kind">Shampoo</span>
    </div>
    <svg class="artwork" style="left:55px; top:620px;" width="395" height="431" viewBox="0 0 395 431" role="img" aria-label="Linienzeichnung einer Frau mit Blattzweig vor pfirsich- und salbeifarbenen Flächen">
      <defs>
        <linearGradient id="care-art" x1="0" y1="0" x2="1" y2="0.3">
          <stop offset="0" stop-color="#fbd7a1"/>
          <stop offset="0.45" stop-color="#fdeedc"/>
          <stop offset="1" stop-color="#cfe5c2"/>
        </linearGradient>
      </defs>
      <rect width="395" height="431" rx="18" fill="url(#care-art)"/>
    </svg>
    <div class="volume">250ml</div>
  </section>

  <section class="label label--balance">
    <svg class="label__shapes" viewBox="0 0 463 1051" aria-hidden="true">
      <path fill="var(--peach)" d="M70 0 L310 0 C318 22 302 40 270 46 C220 56 180 70 130 69 C85 68 63 55 63 30 C63 15 66 6 70 0Z"/>
      <path fill="var(--peach)" d="M310 317 C335 312 365 330 373 355 C378 375 375 405 365 404 C350 386 320 380 300 365 C282 350 283 322 310 317Z"/>
    </svg>
    <div class="brand">Sol Verde</div>
    <div class="product">
      <span class="product__name">Balance</span>
      <span class="product__type">Fettiges Haar</span>
      <span class="product__kind">Shampoo</span>
    </div>
    <svg class="artwork" style="left:0; top:633px;" width="463" height="418" viewBox="0 0 463 418" role="img" aria-label="Linienzeichnung eines Frauenprofils mit Blattzweig vor salbei- und pfirsichfarbenen Flächen">
      <defs>
        <linearGradient id="balance-art" x1="0" y1="0.2" x2="1" y2="0.8">
          <stop offset="0" stop-color="#cfe5c2"/>
          <stop offset="0.55" stop-color="#eef5e8"/>
          <stop offset="1" stop-color="#fbd7a1"/>
        </linearGradient>
      </defs>
      <rect width="463" height="418" fill="url(#balance-art)"/>
    </svg>
    <div class="volume">250ml</div>
  </section>

</main>
</body>
</html>
```